WordPress website design for wealth management company

A modern clean look website for a service company. This is mostly for information only, with a form to capture prospect contact information and schedule a 15 minutes call. There will be several static pages describe what services we offer, how we are different, and a blog section for posting articles and share resources. A section for client testimonials.
I want a website that is easy to understand and maintain. No proprietary plugins that cost extra. The main thing I need help is the visual layout / color palette that present a clean and professional look, select the suitable stock photos that convey the image of trust, professional, innovative, and high service.
Some websites with style I like include the following
- https://www.halvorbrook.com/
- https://www.trivanplanningworks.com/
- https://morvellfunds.com/private-equity-partners/
Also some websites in other industries with clean modern look
- https://zentrell.com/
- https://quovra.com/
- https://www.plumtorvik.com/
I want the end product to be a fully functional website that I can upload into web hosting service I use and I can easily add content and maintain myself in the future.

```html
<!DOCTYPE html>
<html lang="en">
<head>
<meta charset="utf-8">
<title>Harrowgate Wealth</title>
<link rel="stylesheet" href="https://fonts.googleapis.com/css2?family=Poppins:wght@400;500;600;700&display=swap">
<style>
:root{
  --purple:#5a2386;
  --purple-dark:#4a1a72;
  --yellow:#f7b521;
  --ink:#1b1b1b;
  --text:#3a3a3a;
  --paper:#ffffff;
  --cream:#ecebe6;
  --black:#000000;
}
*{box-sizing:border-box;margin:0;padding:0}
html,body{width:1200px;height:4197px;overflow:hidden}
body{font-family:"Poppins",sans-serif;color:var(--text);background:var(--paper);position:relative}
.abs{position:absolute}
.accent{color:var(--yellow)}
.section-title{font-weight:700;font-size:31px;color:var(--ink);text-transform:uppercase;letter-spacing:.3px}

/* header */
.site-header{position:absolute;top:0;left:0;width:1200px;height:133px}
.topbar{position:absolute;top:0;left:0}
.brand{position:absolute;left:110px;top:22px;display:flex;align-items:center;gap:10px}
.brand-dot{width:34px;height:34px;border-radius:50%;background:var(--purple)}
.brand-name{font-weight:600;font-size:22px;color:var(--purple);letter-spacing:2px}
.contact-strip{position:absolute;top:18px;left:480px;display:flex;gap:44px;color:#fff;font-size:13px;font-weight:600}
.contact-strip span{display:flex;align-items:center;gap:10px}
.ico{width:30px;height:30px;border-radius:50%;background:#fff;display:inline-flex;align-items:center;justify-content:center;flex:none}
.main-nav{position:absolute;top:86px;left:490px;display:flex;gap:41px;font-size:15px;color:var(--ink)}
.main-nav a{color:inherit;text-decoration:none}
.main-nav .current{color:var(--purple);font-weight:600;border-bottom:2px solid var(--purple);padding-bottom:2px}

/* hero */
.hero{position:absolute;top:133px;left:0;width:1200px;height:600px}
.hero-title{position:absolute;left:111px;top:205px;font-size:46px;font-weight:700;line-height:52px;color:#fff}
.btn-pill{display:inline-flex;align-items:center;gap:12px;background:var(--yellow);color:#fff;font-weight:600;font-size:14px;border-radius:20px;padding:6px 6px 6px 20px}
.btn-pill i{width:26px;height:26px;border-radius:50%;background:#fff;display:inline-block;border:3px solid var(--purple)}
.btn-dark{background:var(--purple)}
.btn-dark i{border-color:var(--yellow)}
.hero .btn-pill{position:absolute;left:111px;top:328px}
.dots{position:absolute;left:116px;top:452px;display:flex;gap:6px}
.dots b{width:15px;height:15px;border-radius:50%;background:#fff}

/* different */
.different{position:absolute;top:800px;left:0;width:1200px;height:430px}
.different-copy{position:absolute;left:110px;top:14px;width:448px;display:flex;flex-direction:column;align-items:flex-start}
.different-copy p{margin-top:12px;width:448px;font-size:13.6px;line-height:32.5px;text-align:justify}
.different-copy .btn-pill{margin-top:12px}
.different-art{position:absolute;left:730px;top:70px}

/* services */
.services{position:absolute;top:1261px;left:0;width:1200px;height:488px;background:var(--purple);color:#fff;text-align:center}
.services .section-title{color:#fff;margin-top:55px}
.services .lead{font-size:16px;line-height:31px;width:640px;margin:8px auto 0}
.service-item{position:absolute;top:177px;width:220px;text-align:center}
.service-ring{width:210px;height:210px;margin:0 auto;position:relative}
.service-label{font-weight:700;font-size:15px;margin-top:14px}

/* testimonials */
.clients{position:absolute;top:1800px;left:0;width:1200px;height:480px}
.clients .section-title{text-align:center;margin-top:27px}
.photo{background:linear-gradient(160deg,#dedad4,#8d8780)}
.quote-card{position:absolute;left:342px;top:80px;width:505px;height:347px;background:var(--cream);border-left:9px solid var(--yellow)}
.quote-card .name{position:absolute;left:192px;top:26px;font-size:15px;color:var(--ink)}
.quote-card .body{position:absolute;left:192px;top:70px;width:266px;font-size:14px;line-height:31px;text-align:justify;color:var(--ink)}
.quote-card .stars{position:absolute;left:192px;top:295px;font-size:14px;letter-spacing:1px;color:var(--ink)}
.portrait-oval{position:absolute;left:26px;top:50px;width:130px;height:225px;border-radius:65px;border:5px solid var(--purple);background:linear-gradient(180deg,#d8d2cf,#6d5f60)}
.arrow-btn{position:absolute;width:24px;height:24px;border-radius:50%;border:1.5px solid var(--ink);display:flex;align-items:center;justify-content:center}

/* schedule */
.schedule{position:absolute;top:2315px;left:0;width:1200px;height:614px;background:var(--purple);color:#fff;overflow:hidden}
.schedule-photo{position:absolute;left:93px;top:75px;width:335px;height:465px;border-radius:0 90px 0 90px;border:6px solid #fff;border-left:none;border-bottom:none;background:linear-gradient(135deg,#cfc6c0,#f0ede9 55%,#b9b1ab)}
.schedule h2{position:absolute;left:480px;top:70px;font-size:31px;font-weight:500;line-height:41px}
.field{position:absolute;left:482px;width:316px;border-bottom:2px solid #fff;font-weight:600;font-size:15px;padding-bottom:10px}
.schedule .btn-pill{position:absolute;left:482px;top:470px;padding-left:35px;gap:38px}
.contact-box{position:absolute;left:826px;top:82px;width:247px;height:452px;border:3px solid #fff}
.contact-box .cell{height:33.33%;border-bottom:3px solid #fff;padding:34px 0 0 28px;font-size:13px;font-weight:600}
.contact-box .cell:last-child{border-bottom:none}
.contact-box h4{font-size:14px;font-weight:600;margin-bottom:12px}
.contact-box .line{display:flex;gap:10px;align-items:flex-start}
.sq{width:17px;height:17px;background:#fff;border-radius:3px;flex:none}

/* blogs */
.blogs{position:absolute;top:2990px;left:0;width:1200px;height:500px}
.blogs .section-title{text-align:center;margin-top:20px}
.blog-card{position:absolute;top:83px;width:310px;height:400px;border:1px solid #dcdcdc;box-shadow:0 2px 6px rgba(0,0,0,.08);padding:10px}
.blog-img{height:198px}
.blog-meta{display:flex;justify-content:space-between;font-size:13px;font-weight:600;margin:17px 2px 14px}
.blog-meta .tag{color:var(--yellow)}
.blog-meta .date{color:var(--purple);display:flex;gap:6px;align-items:center}
.blog-meta .date i{width:16px;height:15px;background:var(--purple);display:inline-block}
.blog-card p{font-size:14px;line-height:26px;padding:0 2px;color:var(--ink)}
.blog-card .go{position:absolute;right:28px;bottom:22px}

/* newsletter + footer */
.site-footer{position:absolute;top:3653px;left:0;width:1200px;height:544px;background:var(--black);color:#fff}
.newsletter{position:absolute;top:3562px;left:116px;width:976px;height:235px;border-radius:118px;background:var(--purple);color:#fff}
.newsletter h3{position:absolute;left:74px;top:94px;font-size:31px;font-weight:500}
.newsletter p{position:absolute;left:74px;top:140px;width:400px;font-size:14.5px;line-height:29px}
.subscribe{position:absolute;left:532px;top:85px;display:flex;height:60px}
.subscribe span{width:271px;background:#fff;color:var(--ink);font-weight:600;font-size:15px;padding:20px 18px}
.subscribe b{width:115px;background:var(--yellow);font-size:13px;font-weight:600;display:flex;align-items:center;justify-content:center}
.foot-brand{position:absolute;left:112px;top:225px;width:160px;text-align:center}
.foot-brand .brand-dot{width:54px;height:54px;background:#fff;margin:0 auto 16px}
.foot-brand .name{font-size:22px;font-weight:600;letter-spacing:2px;line-height:26px}
.socials{display:flex;gap:9px;justify-content:center;margin-top:18px}
.socials i{width:26px;height:26px;background:#fff;border-radius:4px;display:block}
.foot-col{position:absolute;top:232px;font-size:14px}
.foot-col h5{font-size:16px;font-weight:600;margin-bottom:10px}
.foot-col li{list-style:none;line-height:31px}
.touch li{display:flex;align-items:center;gap:16px;margin-bottom:20px;line-height:17px}
.touch .sqw{width:36px;height:36px;background:#fff;flex:none}
.foot-rule{position:absolute;left:110px;top:480px;width:978px;border-top:1px solid #fff}
.copyright{position:absolute;top:492px;width:1200px;text-align:center;font-size:13px}
</style>
</head>
<body>

<header class="site-header">
  <svg class="topbar" width="1200" height="70" aria-hidden="true"><polygon points="385,0 1200,0 1200,70 455,70" fill="var(--purple)"/></svg>
  <div class="brand"><span class="brand-dot"></span><span class="brand-name">HARROWGATE</span></div>
  <div class="contact-strip">
    <span><i class="ico"><svg width="14" height="14" viewBox="0 0 24 24"><path d="M6 2l4 5-2 3a12 12 0 006 6l3-2 5 4-3 4C10 22 2 14 2 5z" fill="var(--purple)"/></svg></i>+1 555 204 7710</span>
    <span><i class="ico"><svg width="14" height="12" viewBox="0 0 24 18"><rect x="1" y="1" width="22" height="16" fill="none" stroke="var(--purple)" stroke-width="2"/><path d="M1 1l11 9 11-9" fill="none" stroke="var(--purple)" stroke-width="2"/></svg></i>hello@harrowgatewealth.in</span>
    <span><i class="ico"><svg width="12" height="16" viewBox="0 0 16 22"><path d="M8 0a8 8 0 018 8c0 6-8 14-8 14S0 14 0 8a8 8 0 018-8z" fill="var(--purple)"/><circle cx="8" cy="8" r="3" fill="#fff"/></svg></i><span style="display:block;line-height:15px">Linden Row.<br>US - 40218</span></span>
  </div>
  <nav class="main-nav"><a class="current">Home</a><a>About Us</a><a>Services</a><a>Testimonial</a><a>Blog</a><a>Contact Us</a></nav>
</header>

<section class="hero">
  <svg class="abs" width="1200" height="600" style="top:0;left:0">
    <defs><linearGradient id="heroPhoto" x1="0" y1="0" x2="1" y2="1"><stop offset="0" stop-color="#e3e1dc"/><stop offset=".5" stop-color="#a9b3c2"/><stop offset="1" stop-color="#2f4f86"/></linearGradient></defs>
    <polygon points="0,0 612,0 535,592 80,592 0,510" fill="var(--purple)"/>
    <polygon points="612,0 1200,0 1200,592 535,592" fill="var(--yellow)"/>
    <polygon points="619,0 1200,0 1200,592 543,592" fill="url(#heroPhoto)" role="img" aria-label="Team of medical professionals walking through a bright modern hallway"/>
    <polyline points="0,510 80,592 1200,592" fill="none" stroke="#fff" stroke-width="4"/>
    <polyline points="0,514 84,600 1200,600" fill="none" stroke="var(--purple)" stroke-width="4"/>
  </svg>
  <h1 class="hero-title">WELCOME TO<br>HARROWGATE WEALTH</h1>
  <span class="btn-pill">GET STARTED <i></i></span>
  <div class="dots"><b></b><b></b><b></b></div>
</section>

<section class="different">
  <div class="different-copy">
    <h2 class="section-title">How <span class="accent">we are different</span></h2>
    <p>Lorem ipsum dolor sit amet, consectetur adipiscing elit, sed do eiusmod tempor incididunt ut labore et dolore magna aliqua. Ut enim ad minim veniam, quis nostrud exercitation ullamco laboris nisi ut aliquip ex ea commodo consequat. Duis aute irure dolor in reprehenderit in voluptate velit esse cillum dolore eu fugiat nulla pariatur. Excepteur sint occaecat cupidatat non proident, sunt in culpa qui officia deserunt mollit anim id est laborum.</p>
    <span class="btn-pill btn-dark">GET STARTED <i></i></span>
  </div>
  <svg class="different-art" width="310" height="280" role="img" aria-label="Circular photo of a team meeting in a modern office">
    <defs><linearGradient id="meet" x1="0" y1="0" x2="1" y2="1"><stop offset="0" stop-color="#e6e3df"/><stop offset="1" stop-color="#7b7f8c"/></linearGradient></defs>
    <circle cx="155" cy="140" r="135" fill="url(#meet)"/>
    <path d="M255 60 A120 120 0 1 0 250 220" fill="none" stroke="var(--purple)" stroke-width="10"/>
  </svg>
</section>

<section class="services">
  <h2 class="section-title">Services we offer</h2>
  <p class="lead">Lorem ipsum dolor sit amet, consectetur adipiscing elit, sed do eiusmod tempor incididunt ut labore et dolore magna aliqua.</p>
  <div class="service-item" style="left:148px">
    <svg class="service-ring" viewBox="0 0 210 210"><path d="M15 115 A90 90 0 1 1 195 115" fill="none" stroke="#fff" stroke-width="4"/><circle cx="105" cy="105" r="100" fill="none" stroke="#fff" stroke-width="2" stroke-dasharray="6 5"/><circle cx="105" cy="105" r="82" fill="#fff"/><path d="M82 100c0-15 20-20 23-6 3-14 23-9 23 6 0 14-23 28-23 28S82 114 82 100z" fill="none" stroke="var(--purple)" stroke-width="3"/><path d="M86 106h10l5-8 6 14 4-6h10" fill="none" stroke="var(--purple)" stroke-width="2.5"/></svg>
    <div class="service-label">LOREM IPSUM</div>
  </div>
  <div class="service-item" style="left:482px">
    <svg class="service-ring" viewBox="0 0 210 210"><path d="M15 115 A90 90 0 1 1 195 115" fill="none" stroke="#fff" stroke-width="4"/><circle cx="105" cy="105" r="100" fill="none" stroke="#fff" stroke-width="2" stroke-dasharray="6 5"/><circle cx="105" cy="105" r="82" fill="var(--yellow)"/><rect x="82" y="80" width="40" height="50" rx="3" fill="none" stroke="var(--purple)" stroke-width="3"/><path d="M98 108h16M106 100v16" stroke="var(--purple)" stroke-width="3"/></svg>
    <div class="service-label">LOREM IPSUM</div>
  </div>
  <div class="service-item" style="left:816px">
    <svg class="service-ring" viewBox="0 0 210 210"><path d="M15 115 A90 90 0 1 1 195 115" fill="none" stroke="#fff" stroke-width="4"/><circle cx="105" cy="105" r="100" fill="none" stroke="#fff" stroke-width="2" stroke-dasharray="6 5"/><circle cx="105" cy="105" r="82" fill="#fff"/><path d="M105 80l20 7v15c0 14-10 22-20 26-10-4-20-12-20-26V87z" fill="none" stroke="var(--ink)" stroke-width="3"/><path d="M97 105h16M105 97v16" stroke="var(--ink)" stroke-width="3"/></svg>
    <div class="service-label">LOREM IPSUM</div>
  </div>
</section>

<section class="clients">
  <h2 class="section-title">What our <span class="accent">clients says</span></h2>
  <div class="abs photo" style="left:110px;top:80px;width:225px;height:347px" role="img" aria-label="Portrait of a smiling businesswoman holding a folder"></div>
  <div class="quote-card">
    <div class="portrait-oval" role="img" aria-label="Portrait of the client giving the testimonial"></div>
    <div class="name">Marisol</div>
    <p class="body">❝ Lorem ipsum dolor sit amet, consectetur adipiscing elit, sed do eiusmod tempor incididunt ut labore et dolore magna aliqua. Ut enim ad minim veniam, quis nostrud exercitation ullamco laboris nisi ut aliquip ex ea commodo consequat.</p>
    <div class="stars">★★★★★</div>
  </div>
  <div class="abs photo" style="left:861px;top:80px;width:225px;height:347px" role="img" aria-label="Portrait of a senior businesswoman with glasses"></div>
  <span class="arrow-btn" style="left:42px;top:249px"><svg width="10" height="10" viewBox="0 0 10 10"><path d="M7 1L3 5l4 4" fill="none" stroke="#000" stroke-width="1.6"/></svg></span>
  <span class="arrow-btn" style="left:1133px;top:249px"><svg width="10" height="10" viewBox="0 0 10 10"><path d="M3 1l4 4-4 4" fill="none" stroke="#000" stroke-width="1.6"/></svg></span>
</section>

<section class="schedule">
  <div class="schedule-photo" role="img" aria-label="Smiling support advisor wearing a headset at a desk"></div>
  <h2>schedule a 15<br>minutes cal</h2>
  <div class="field" style="top:180px">Full Name</div>
  <div class="field" style="top:263px">Email</div>
  <div class="field" style="top:361px">Message</div>
  <span class="btn-pill">SUBMIT <i></i></span>
  <div class="contact-box">
    <div class="cell"><h4>EMAIL US</h4><div class="line"><i class="sq"></i>hello@harrowgatewealth.in</div></div>
    <div class="cell"><h4>LOCATED IN</h4><div class="line"><i class="sq"></i><span>Linden Row.<br>US - 40218</span></div></div>
    <div class="cell"><h4>CALL US</h4><div class="line"><i class="sq"></i>+1 555 204 7710</div></div>
  </div>
</section>

<section class="blogs">
  <h2 class="section-title">Recent <span class="accent">blogs</span></h2>
  <article class="blog-card" style="left:110px">
    <div class="blog-img photo" role="img" aria-label="Advisors meeting with clients at a reception desk"></div>
    <div class="blog-meta"><span class="tag">LOREM IPSUM</span><span class="date"><i></i>AUG 17 2023</span></div>
    <p>Lorem ipsum dolor sit amet, consectetur adipiscing elit, sed do eiusmod tempor incididunt ut labore et dolore magna aliqua.</p>
    <svg class="go" width="30" height="12"><path d="M0 6h27M21 1l6 5-6 5" fill="none" stroke="var(--purple)" stroke-width="2.5"/></svg>
  </article>
  <article class="blog-card" style="left:445px">
    <div class="blog-img photo" role="img" aria-label="Two women in conversation"></div>
    <div class="blog-meta"><span class="tag">LOREM IPSUM</span><span class="date"><i></i>AUG 17 2023</span></div>
    <p>Lorem ipsum dolor sit amet, consectetur adipiscing elit, sed do eiusmod tempor incididunt ut labore et dolore magna aliqua.</p>
    <svg class="go" width="30" height="12"><path d="M0 6h27M21 1l6 5-6 5" fill="none" stroke="var(--purple)" stroke-width="2.5"/></svg>
  </article>
  <article class="blog-card" style="left:780px">
    <div class="blog-img photo" role="img" aria-label="Nurse caring for an elderly patient in bed"></div>
    <div class="blog-meta"><span class="tag">LOREM IPSUM</span><span class="date"><i></i>AUG 17 2023</span></div>
    <p>Lorem ipsum dolor sit amet, consectetur adipiscing elit, sed do eiusmod tempor incididunt ut labore et dolore magna aliqua.</p>
    <svg class="go" width="30" height="12"><path d="M0 6h27M21 1l6 5-6 5" fill="none" stroke="var(--purple)" stroke-width="2.5"/></svg>
  </article>
  <span class="arrow-btn" style="left:42px;top:285px"><svg width="10" height="10" viewBox="0 0 10 10"><path d="M7 1L3 5l4 4" fill="none" stroke="#000" stroke-width="1.6"/></svg></span>
  <span class="arrow-btn" style="left:1133px;top:285px"><svg width="10" height="10" viewBox="0 0 10 10"><path d="M3 1l4 4-4 4" fill="none" stroke="#000" stroke-width="1.6"/></svg></span>
</section>

<footer class="site-footer">
  <div class="foot-brand">
    <div class="brand-dot"></div>
    <div class="name">HARROWGATE</div>
    <div class="socials"><i></i><i></i><i></i><i></i></div>
  </div>
  <div class="foot-col" style="left:382px;top:225px"><h5>QUICK LINKS</h5><ul><li>Home</li><li>About Us</li><li>Services</li><li>Testimonials</li><li>Blog</li><li>Contact</li></ul></div>
  <div class="foot-col" style="left:600px"><h5>HELP LINKS</h5><ul><li>Privacy Policy</li><li>Terms &amp; Conditions</li></ul></div>
  <div class="foot-col touch" style="left:858px"><h5>GET IN TOUCH</h5><ul><li><i class="sqw"></i><span>Linden Row.<br>US - 40218</span></li><li><i class="sqw"></i>+1 555 204 7710</li><li><i class="sqw"></i>hello@harrowgatewealth.in</li></ul></div>
  <div class="foot-rule"></div>
  <div class="copyright">© Copyright 2023 Harrowgate Wealth . All Rights Reserved.</div>
</footer>

<section class="newsletter">
  <h3>SIGN UP FOR NWESLETTER</h3>
  <p>Subscribe to our newsletter to get the latest update to your inbox</p>
  <div class="subscribe"><span>Enter Your Email</span><b>SUBSCRIBE</b></div>
</section>

</body>
</html>
```